Vortaleen - Lead the Way!

Vortaleen is a new Silicon Valley company, of the pimrela founders from Berlin, which provides a "Shared Hive Circle". This platform allows the crowd to support startups with money, experts and fame. Our Vision is, that everyone should become an entrepreneur.

Pls find all brief details in the attached document
Updates

Would be nice to have a list of more social services I'm available on, like a list of pictograms of all my services:

Find me on: chattro, fennwix+, qrt, mivrel, datebloom, pohk, rplex, etc...

pls make sure to use the right font:
http://www.typelarder-demo.com/fonts/Orbitron

Target Market(s)

Main target market is those already involved in the startup industry, by fundraising, investing, advising, cofounding and working. Vortaleen brings a totaly new transparency and collaborative way of starting companies to that business.

· Entrepreneurs (looking for funding, team and community)
· Investors (looking for hot investments and )
· Experts (workers looking for startups they can work for equity)
· Incubators & Business Schools (looking for tools to advise startups)

Industry/Entity Type

It Company

Requirements
Must have
• Pls find all brief details in the attached document
Nice to have

```html
<!DOCTYPE html>
<html lang="en">
<head>
<meta charset="utf-8">
<title>Vortaleen – Business Card</title>
<link rel="stylesheet" href="https://fonts.googleapis.com/css2?family=Orbitron:wght@900&family=Arimo:wght@400;700&display=swap">
<style>
  :root {
    --red: #e8402a;
    --slate: #5f7280;
    --slate-dark: #4b6070;
    --panel-light: #dde1e2;
    --panel-mid: #c9cfd1;
    --panel-dark: #b7bec1;
    --ink: #45494d;
    --page: #ffffff;
  }
  * { margin: 0; padding: 0; box-sizing: border-box; }
  html, body { width: 1200px; height: 363px; overflow: hidden; background: var(--page); }
  body { position: relative; font-family: "Arimo", Arial, sans-serif; color: var(--ink); }

  .card { position: absolute; top: 11px; width: 587px; height: 342px; background: var(--slate); overflow: hidden; }
  .card--front { left: 9px; }
  .card--back { left: 604px; }
  .card__accent { position: absolute; top: 0; bottom: 0; width: 193px; background: var(--red); }
  .card--front .card__accent { left: 0; }
  .card--back .card__accent { right: 0; width: 230px; }

  .card__panel { position: absolute; top: 21px; height: 291px; width: 535px; }
  .card--front .card__panel { left: 32px; }
  .card--back .card__panel { left: 19px; }
  .card__pattern {
    position: absolute; inset: 0;
    background: radial-gradient(ellipse at 45% 45%, var(--panel-light) 0%, var(--panel-mid) 60%, var(--panel-dark) 100%);
  }

  .abs { position: absolute; white-space: nowrap; }

  /* front */
  .brand-name { left: 29px; top: 60px; font-family: "Orbitron", sans-serif; font-weight: 900; font-size: 50px; letter-spacing: 1px; color: var(--red); line-height: 1; }
  .brand-tagline { left: 270px; top: 111px; font-weight: 700; font-size: 17px; color: var(--slate-dark); }
  .brand-dot { left: 88px; top: 125px; width: 62px; height: 62px; border-radius: 50%; background: var(--red); }
  .person-name { left: 271px; top: 158px; font-size: 20px; color: var(--red); }
  .person-role { left: 338px; top: 181px; font-size: 9px; color: var(--ink); }
  .contact { position: absolute; left: 230px; top: 194px; }
  .contact__row { display: flex; align-items: center; height: 15px; }
  .contact__label { width: 81px; text-align: right; font-size: 6.5px; text-transform: uppercase; color: var(--red); letter-spacing: .3px; }
  .contact__dot { width: 4px; height: 4px; background: var(--red); border-radius: 50%; margin: 0 6px 0 4px; }
  .contact__value { font-size: 13px; color: var(--ink); }

  .social { position: absolute; top: 266px; left: 15px; display: flex; gap: 40px; font-size: 11px; color: var(--ink); }
  .social__item { display: flex; align-items: center; gap: 5px; }
  .social__mark { width: 10px; height: 10px; background: var(--red); }

  /* back */
  .pitch-title { left: 91px; top: 26px; font-weight: 700; font-size: 13px; color: var(--red); }
  .pitch-list { position: absolute; left: 147px; top: 45px; list-style: none; font-size: 11px; line-height: 14px; color: var(--ink); }
  .star { color: var(--red); margin-right: 6px; font-size: 9px; }
  .pitch-join { left: 91px; top: 89px; font-weight: 700; font-size: 12.5px; color: var(--red); }
  .notes { position: absolute; left: 209px; top: 110px; width: 254px; list-style: none; font-size: 10px; line-height: 13.5px; color: var(--ink); }
  .notes li { display: flex; align-items: baseline; }
  .notes__line { flex: 1; border-bottom: 1px dashed var(--ink); margin-left: 2px; height: 8px; }
  .sign-off { left: 91px; top: 200px; font-size: 13px; color: var(--ink); }
  .sign-off b { color: var(--red); }
  .address { position: absolute; left: 91px; top: 218px; font-size: 12.5px; line-height: 17px; color: var(--ink); }
  .web-big { left: 0; width: 535px; text-align: center; top: 256px; font-weight: 700; font-size: 15px; letter-spacing: 5px; color: var(--red); padding-left: 40px; }
</style>
</head>
<body>

<section class="card card--front" aria-label="Business card front">
  <div class="card__accent"></div>
  <div class="card__panel">
    <div class="card__pattern" role="img" aria-label="Soft grey pixel-invader background pattern"></div>
    <div class="abs brand-name">VORTALEEN</div>
    <div class="abs brand-tagline">LEAD THE WAY!</div>
    <div class="abs brand-dot"></div>
    <div class="abs person-name">Lennart Vosk</div>
    <div class="abs person-role">Founder and CEO</div>
    <div class="contact">
      <div class="contact__row"><span class="contact__label">Email</span><span class="contact__dot"></span><span class="contact__value">lvo@vortaleen.com</span></div>
      <div class="contact__row"><span class="contact__label">Mobile</span><span class="contact__dot"></span><span class="contact__value">000.000.0000</span></div>
      <div class="contact__row"><span class="contact__label">Website</span><span class="contact__dot"></span><span class="contact__value">www.vortaleen.com</span></div>
    </div>
    <div class="social">
      <span class="social__item"><span class="social__mark"></span>flockbook.com/lennartvosk</span>
      <span class="social__item"><span class="social__mark"></span>www.chattro.com/lennartvosk</span>
      <span class="social__item"><span class="social__mark"></span>chirpr.com/lennart_vosk</span>
    </div>
  </div>
</section>

<section class="card card--back" aria-label="Business card back">
  <div class="card__accent"></div>
  <div class="card__panel">
    <div class="card__pattern" role="img" aria-label="Soft grey pixel-invader background pattern"></div>
    <div class="abs pitch-title">ARE YOU INTERESTED IN?</div>
    <ul class="pitch-list">
      <li><span class="star">★</span>Starting your in Business?</li>
      <li><span class="star">★</span>Investing in hot Startups?</li>
      <li><span class="star">★</span>Working for the next “Flockbook”?</li>
    </ul>
    <div class="abs pitch-join">JOIN US ON FLOCKBOOK.COM/VORTALEEN</div>
    <ul class="notes">
      <li><span class="star">★</span>date and event<span class="notes__line"></span></li>
      <li><span class="star">★</span>keywords,<span class="notes__line"></span></li>
      <li><span class="star">★</span>follow up,<span class="notes__line"></span></li>
      <li><span class="star">★</span><span class="notes__line"></span></li>
    </ul>
    <div class="abs sign-off"><b>VORTALEEN</b> - Lead the Way!</div>
    <div class="address">
      Berlin - Lindenhofer Weg 22 / 10999 Berlin / Germany<br>
      Silicon valley - 218 Orchard Loop / Sunnyvale / CA 94086
    </div>
    <div class="abs web-big">WWW.VORTALEEN.COM</div>
  </div>
</section>

</body>
</html>
```